A new presentation to our clients

we are a Real Estate agency, our website is www.lumibrasa.com and it’s time to have a new, fashion and remarcable Business Card. we want to differentiate ourselves from other companies so we want a business card that differentiates us. we want the business card to impact our customers. in the competitive market that we have today, we have to be different and it is this difference that we seek

Target Market(s)

Real Estate Clients

Contact Information for Business Card

We search a totaly diferent card from the usual

Font styles to use
Sans Serif

Colors
e34197

Requirements
Must have
• Logo, adress, phone contact, e-mail, photo, and our website
Nice to have
• We would like to see a modern business card
Should not have
• Houses or building draws

```html
<!DOCTYPE html>
<html lang="en">
<head>
<meta charset="utf-8">
<title>Lumibrasa Business Card</title>
<link href="https://fonts.googleapis.com/css2?family=Questrial&display=swap" rel="stylesheet">
<style>
  :root {
    --brand-pink: #e8297a;
    --card-white: #ffffff;
    --ink: #1a1a1a;
    --swoosh-dark: #222222;
    --swoosh-grey: #9a9a9a;
    --backdrop: #4a4c50;
    --photo-light: #e9e6e4;
    --photo-dark: #2b2a2c;
  }
  * { margin: 0; padding: 0; box-sizing: border-box; }
  html, body { width: 1200px; height: 874px; overflow: hidden; }
  body {
    background: var(--backdrop);
    font-family: "Questrial", sans-serif;
    position: relative;
  }
  .card {
    position: absolute;
    left: 260px;
    width: 680px;
    height: 390px;
    border-radius: 34px;
    overflow: hidden;
  }
  .card-back { top: 35px; background: var(--brand-pink); }
  .card-front { top: 449px; background: var(--card-white); }
  .card svg { display: block; width: 100%; height: 100%; }
  .notch { fill: var(--card-white); }
  .back-wordmark {
    position: absolute; inset: 0;
    display: flex; align-items: center; justify-content: center;
    color: var(--card-white); font-size: 92px; letter-spacing: 1px;
  }
  .front-wordmark {
    position: absolute; left: 40px; top: 76px;
    color: var(--brand-pink); font-size: 56px; letter-spacing: 1px;
  }
  .person-name {
    position: absolute; left: 60px; top: 168px;
    color: var(--ink); font-size: 34px;
  }
  .person-role {
    position: absolute; left: 62px; top: 210px;
    color: var(--brand-pink); font-size: 17px;
  }
  .contact-block {
    position: absolute; left: 122px; top: 298px;
    border-left: 2px solid var(--card-white);
    padding-left: 14px;
    color: var(--card-white); font-size: 16px; line-height: 21px;
  }
  .contact-line { display: flex; align-items: center; gap: 7px; }
  .contact-line svg { width: 13px; height: 13px; fill: var(--card-white); }
  .website {
    position: absolute; right: 30px; top: 250px;
    color: var(--card-white); font-size: 15px;
  }
</style>
</head>
<body>

<section class="card card-back">
  <svg viewBox="0 0 680 390" aria-hidden="true">
    <circle class="notch" cx="0" cy="340" r="26"/>
    <circle class="notch" cx="680" cy="50" r="26"/>
  </svg>
  <div class="back-wordmark">Lumibrasa</div>
</section>

<section class="card card-front">
  <svg viewBox="0 0 680 390">
    <defs>
      <linearGradient id="portraitTone" x1="0" y1="0" x2="0" y2="1">
        <stop offset="0" stop-color="var(--card-white)"/>
        <stop offset="0.35" stop-color="var(--photo-light)"/>
        <stop offset="1" stop-color="var(--photo-dark)"/>
      </linearGradient>
    </defs>
    <rect class="portrait" x="430" y="0" width="250" height="225" fill="url(#portraitTone)" role="img" aria-label="Portrait photo of the agency director"/>
    <path d="M0 284 C150 234 260 220 380 214 C500 206 610 180 680 112 L680 126 C610 192 500 218 380 226 C260 232 150 248 0 300 Z" fill="var(--swoosh-dark)"/>
    <path d="M380 210 C500 202 610 174 680 100 L680 114 C610 186 500 212 380 218 Z" fill="var(--swoosh-grey)"/>
    <path d="M0 300 C150 248 260 232 380 226 C500 218 610 192 680 126 L680 390 L0 390 Z" fill="var(--brand-pink)"/>
  </svg>
  <div class="front-wordmark">Lumibrasa</div>
  <div class="person-name">Daniel Ward</div>
  <div class="person-role">Director</div>
  <div class="contact-block">
    <div>48 Harbour Lane, Suite B</div>
    <div>Leeds, UK LS1 4QT</div>
    <div class="contact-line">
      <svg viewBox="0 0 24 24" aria-hidden="true"><path d="M6.6 10.8a15 15 0 0 0 6.6 6.6l2.2-2.2c.3-.3.7-.4 1-.2 1.1.4 2.3.6 3.6.6.6 0 1 .4 1 1V20c0 .6-.4 1-1 1A17 17 0 0 1 3 4c0-.6.4-1 1-1h3.5c.6 0 1 .4 1 1 0 1.3.2 2.5.6 3.6.1.3 0 .7-.2 1z"/></svg>
      020 413 8852
    </div>
    <div class="contact-line">
      <svg viewBox="0 0 24 24" aria-hidden="true"><path d="M2 5h20v14H2z M2 5l10 8 10-8" fill="none" stroke="#fff" stroke-width="2.4"/></svg>
      info@lumibrasa.com
    </div>
  </div>
  <div class="website">www.lumibrasa.com</div>
</section>

</body>
</html>
```